Small Business Broker Business Card Design

A business card design for a small business brokerage, which is a financial service, not unlike real estate brokerage, but for small businesses such as laundromats, pizza shops, restaurants, cleaners etc. The designs should all be simple, more conservative in nature, using the colors and font of the logo. Again, think real estate Brokerage as a business context
Contact Information for Business Card
Name: Glen R. Harlow. Title: Small Business Advisor. Email: g.harlow@bayfieldcapitalworks.example. Mobile: (555) 274-3918. Office: (555) 806-2147. www.bayfieldcapitalworks.example

```html
<!DOCTYPE html>
<html lang="en">
<head>
<meta charset="utf-8">
<title>Bayfield Capital Works – Business Card</title>
<link href="https://fonts.googleapis.com/css2?family=Questrial&family=Open+Sans:wght@400;700&display=swap" rel="stylesheet">
<style>
  :root {
    --backdrop: #9a9a9a;
    --navy: #1a3a68;
    --green: #8cc63f;
    --green-soft: #b9dc8a;
    --white: #ffffff;
    --divider: rgba(255,255,255,0.35);
  }
  html, body {
    margin: 0;
    width: 1200px;
    height: 1200px;
    overflow: hidden;
    background: var(--backdrop);
  }
  .canvas { position: relative; width: 1200px; height: 1200px; }
  .card {
    position: absolute;
    left: 226px;
    width: 746px;
    height: 436px;
  }
  .card--front { top: 141px; background: var(--white); }
  .card--back { top: 659px; background: var(--navy); }

  .brand { position: absolute; }
  .brand__square { display: block; }
  .brand__name {
    font-family: "Questrial", sans-serif;
    text-transform: uppercase;
    white-space: nowrap;
    letter-spacing: 0.5px;
  }
  .brand__tagline {
    font-family: "Questrial", sans-serif;
    text-transform: uppercase;
    color: var(--green);
    white-space: nowrap;
    letter-spacing: 1.4px;
  }

  /* front */
  .card--front .brand { left: 95px; top: 184px; display: flex; align-items: center; gap: 22px; }
  .card--front .brand__square { background: var(--navy); width: 58px; height: 58px; }
  .card--front .brand__name {
    color: var(--navy); font-size: 25px; line-height: 30px;
    -webkit-text-stroke: 0.6px var(--navy);
  }
  .card--front .brand__tagline {
    font-size: 11.5px; margin-top: 2px;
    -webkit-text-stroke: 0.3px var(--green);
  }

  /* back, left column */
  .card--back .brand { left: 0; width: 348px; top: 158px; text-align: center; }
  .card--back .brand__square {
    margin: 0 auto 22px;
    width: 50px; height: 50px; background: var(--white);
  }
  .card--back .brand__name {
    color: var(--white); font-size: 17px; line-height: 20px;
    -webkit-text-stroke: 0.3px var(--white);
  }
  .card--back .brand__tagline { font-size: 8.4px; margin-top: 3px; letter-spacing: 0.9px; }

  .divider {
    position: absolute; left: 348px; top: 113px;
    width: 1px; height: 210px; background: var(--divider);
  }

  .contact { position: absolute; left: 376px; top: 150px; color: var(--white); }
  .contact__name {
    font-family: "Questrial", sans-serif;
    font-size: 24px; line-height: 28px;
    text-transform: uppercase; letter-spacing: 0.5px;
    -webkit-text-stroke: 0.6px var(--white);
  }
  .contact__title {
    font-family: "Questrial", sans-serif;
    color: var(--green); font-size: 13px; letter-spacing: 0.8px;
    text-transform: uppercase; margin-top: 1px;
    -webkit-text-stroke: 0.3px var(--green);
  }
  .contact__lines {
    font-family: "Open Sans", sans-serif;
    font-size: 16px; line-height: 25px; margin-top: 20px;
  }
  .contact__lines b { font-weight: 700; }

  .website {
    position: absolute; left: 0; right: 0; top: 392px;
    text-align: center;
    font-family: "Open Sans", sans-serif; font-size: 17px;
    color: var(--green); font-weight: 700;
  }
  .website__tld { font-weight: 400; color: var(--green-soft); }
</style>
</head>
<body>
<main class="canvas">
  <section class="card card--front" aria-label="Card front">
    <div class="brand">
      <span class="brand__square"></span>
      <div>
        <div class="brand__name">Bayfield Capital Works, Inc</div>
        <div class="brand__tagline">Trusted guidance to sell or acquire your local firm</div>
      </div>
    </div>
  </section>

  <section class="card card--back" aria-label="Card back">
    <div class="brand">
      <span class="brand__square"></span>
      <div class="brand__name">Bayfield Capital Works, Inc</div>
      <div class="brand__tagline">Trusted guidance to sell or acquire your local firm</div>
    </div>

    <div class="divider"></div>

    <div class="contact">
      <div class="contact__name">Glen R. Harlow</div>
      <div class="contact__title">Small Business Advisor</div>
      <div class="contact__lines">
        <div>g.harlow@bayfieldcapitalworks.example</div>
        <div><b>Mobile:</b> (555) 274-3918</div>
        <div><b>Office:</b> (555) 806-2147</div>
      </div>
    </div>

    <div class="website">bayfieldcapitalworks<span class="website__tld">.example</span></div>
  </section>
</main>
</body>
</html>
```